dsadasdasdasdsa

Industry/Entity Type

Mortgage Broking

Requirements
Must have
• Call-to-action button somewhere on the graphic
Nice to have
• The font of our logo is Montserrat

```html
<!DOCTYPE html>
<html lang="en">
<head>
<meta charset="UTF-8">
<title>Mortgage Broker Directory Banner</title>
<link href="https://fonts.googleapis.com/css2?family=Montserrat:wght@600;700;800;900&display=swap" rel="stylesheet">
<style>
  :root {
    --green-deep: #0f5a35;
    --green-mid: #1b7a45;
    --green-light: #2e9a55;
    --mint: #e9f6e4;
    --mint-soft: #d3ecc9;
    --red-deep: #b8321e;
    --red-bright: #e2502c;
    --orange: #ef6a3a;
    --yellow: #f7ea1a;
    --white: #ffffff;
  }
  * { margin: 0; padding: 0; box-sizing: border-box; }
  html, body { width: 1200px; height: 180px; overflow: hidden; background: var(--white); }
  .banner {
    position: relative;
    width: 1200px;
    height: 180px;
    overflow: hidden;
    font-family: "Montserrat", sans-serif;
  }
  .banner-backdrop { position: absolute; inset: 0; }
  .mascot-area {
    position: absolute;
    left: 690px;
    top: 0;
    width: 250px;
    height: 180px;
    background: linear-gradient(180deg, var(--mint) 0%, var(--mint-soft) 100%);
  }
  .headline-block {
    position: absolute;
    left: 26px;
    top: 22px;
    color: var(--white);
  }
  .headline-question {
    color: var(--yellow);
    font-weight: 600;
    font-size: 26px;
    line-height: 1;
    letter-spacing: 0.2px;
  }
  .headline-divider {
    width: 520px;
    margin: 16px 0 12px;
    border-top: 3px dotted var(--green-light);
    opacity: 0.9;
  }
  .headline-line {
    font-weight: 900;
    text-transform: uppercase;
    line-height: 1.05;
  }
  .headline-line--upper { font-size: 30px; letter-spacing: 0.2px; }
  .headline-line--lower { font-size: 38px; letter-spacing: 0.3px; }
  .cta-button {
    position: absolute;
    left: 1030px;
    top: 73px;
    width: 136px;
    height: 40px;
    border-radius: 20px;
    background: var(--yellow);
    color: var(--green-deep);
    font-weight: 800;
    font-size: 16px;
    display: flex;
    align-items: center;
    justify-content: center;
    text-decoration: none;
  }
</style>
</head>
<body>
  <div class="banner">
    <svg class="banner-backdrop" width="1200" height="180" viewBox="0 0 1200 180" aria-hidden="true">
      <defs>
        <linearGradient id="mintWash" x1="0" y1="0" x2="1" y2="0">
          <stop offset="0" stop-color="#ffffff"/>
          <stop offset="1" stop-color="#d7efcf"/>
        </linearGradient>
        <linearGradient id="greenPanel" x1="0" y1="0" x2="1" y2="0">
          <stop offset="0" stop-color="#0d5230"/>
          <stop offset="1" stop-color="#13683c"/>
        </linearGradient>
        <linearGradient id="redPanel" x1="0" y1="0" x2="1" y2="0">
          <stop offset="0" stop-color="#c63a22"/>
          <stop offset="1" stop-color="#e6552f"/>
        </linearGradient>
      </defs>
      <rect width="1200" height="180" fill="url(#mintWash)"/>
      <polygon points="620,0 690,0 640,180 570,180" fill="#2f9a52" opacity="0.6"/>
      <polygon points="0,0 630,0 580,180 0,180" fill="url(#greenPanel)"/>
    </svg>

    <div class="mascot-area" role="img" aria-label="Friendly cartoon turtle mascot holding a small house"></div>

    <svg class="banner-backdrop" width="1200" height="180" viewBox="0 0 1200 180" aria-hidden="true">
      <defs>
        <linearGradient id="redPanelFront" x1="0" y1="0" x2="1" y2="0">
          <stop offset="0" stop-color="#c63a22"/>
          <stop offset="1" stop-color="#e6552f"/>
        </linearGradient>
      </defs>
      <polygon points="960,0 1200,0 1200,180 880,180" fill="url(#redPanelFront)"/>
      <polygon points="960,0 985,0 905,180 880,180" fill="#f08a5a" opacity="0.55"/>
      <polygon points="1140,0 1200,0 1200,180 1080,180" fill="#ef6a3a" opacity="0.5"/>
    </svg>

    <div class="headline-block">
      <p class="headline-question">Need a Mortgage Broker?</p>
      <div class="headline-divider"></div>
      <p class="headline-line headline-line--upper">Search now on Australia’s</p>
      <p class="headline-line headline-line--lower">Largest Directory</p>
    </div>

    <a class="cta-button" href="#">CLICK HERE</a>
  </div>
</body>
</html>
```